Revamp Of Landing Page For an Automated AI Voice Agents Agency

here is my current landing page https://app.brightfernpromotionhub.biz/v2/preview/WXKRPmQ4hLzYBvNdTeGS?notrack=true

Please use all my current content and imagery of ai agents in your new design. Make it easy to ready, easy to navigate and easy to understand

I am looking for a SLEEK shiny polished looking website. I like Dark themed sites but am open to see light themed sites too so please dont be shy.

The site should have an Ai Voice Agent Theme about it. Maybe look and feel of futureistic but simple and not intimidating to the average person...

Here are a couple website designs I like for reference:
https://q7v.io/
https://ai-bots.marekholvin.com/
https://chatwelmo.com/ai-agents

Target Market(s)

b2b

Industry/Entity Type

AI Voice Agents

Coding

Coded - Design and coding required

Font styles to use
Other font styles liked:
• open

Requirements
Must have
• all elements and content and images used in existing design.
Nice to have
• open
Should not have
• open

```html
<!DOCTYPE html>
<html lang="en">
<head>
<meta charset="utf-8">
<title>Voxwell – AI Voice Agents</title>
<link href="https://fonts.googleapis.com/css2?family=Outfit:wght@300;400;500;600&display=swap" rel="stylesheet">
<style>
:root{
  --bg-hero:#1c1a1f;
  --bg-band:#18161c;
  --bg-main:#0f0e12;
  --bg-footer:#1c1a20;
  --card:#1b191f;
  --text:#ffffff;
  --muted:#a9a6b0;
  --purple:#8d3fdb;
  --blue:#5a3df2;
  --btn-a:#4a36f2;
  --btn-b:#8a2fd6;
  --line:#2a2830;
  --star:#f4b73a;
}
*{box-sizing:border-box;margin:0;padding:0}
html,body{width:1200px;height:4231px;overflow:hidden}
body{background:var(--bg-main);color:var(--text);font-family:"Outfit",sans-serif;position:relative}
.abs{position:absolute}
.center{left:0;width:1200px;text-align:center}
.hl-purple{color:var(--purple)}
.hl-blue{color:var(--blue)}
h1,h2,h3,h4{font-weight:500;text-transform:uppercase;letter-spacing:-.3px}
.section-title{font-size:27px}
.lede{font-size:13px;line-height:34px;color:var(--muted)}
.btn{display:flex;align-items:center;justify-content:center;height:42px;border-radius:4px;background:linear-gradient(90deg,var(--btn-a),var(--btn-b));color:#fff;font-size:14px;text-transform:uppercase;text-decoration:none;font-weight:400}
.btn-center{left:468px;width:264px}

.hero{position:absolute;left:0;top:0;width:1200px;height:573px;background:var(--bg-hero)}
.brand{left:112px;top:60px;display:flex;align-items:center;gap:12px;font-size:38px;font-weight:400;letter-spacing:2px}
.brand-dot{width:20px;height:20px;border-radius:50%;border:2px solid #fff}
.hero-title{left:112px;top:160px;width:700px;font-size:20px;line-height:46px;font-weight:500}
.hero-copy{left:112px;top:306px;width:620px;font-size:13px;line-height:34px;color:var(--muted)}
.hero-art{left:829px;top:33px;width:371px;height:540px;background:radial-gradient(circle at 55% 40%,#3a7bd5 0%,#3a2a8a 35%,#221a3a 65%,var(--bg-hero) 90%)}

.workforce{position:absolute;left:0;top:573px;width:1200px;height:637px;background:var(--bg-band)}
.agent-card{top:895px;width:305px;height:238px;background:var(--card);border-radius:8px;padding:30px 30px}
.icon-dot{width:50px;height:50px;border-radius:50%;background:linear-gradient(135deg,var(--btn-a),var(--btn-b));display:flex;align-items:center;justify-content:center}
.agent-card h3{font-size:16px;margin-top:38px}
.agent-card p{font-size:13px;line-height:34px;color:var(--muted);margin-top:12px}
.nav-arrow{top:1000px;font-size:30px;color:#fff}
.card-go{width:42px;height:42px;border-radius:50%;background:var(--purple);display:flex;align-items:center;justify-content:center}

.install-art{left:112px;top:1294px;width:346px;height:372px;border-radius:14px;background:linear-gradient(135deg,#4d2fd6,#7a2fd0 60%,#5a2bc4)}
.install-glow{left:300px;top:1200px;width:700px;height:560px;background:radial-gradient(ellipse at center,rgba(80,50,200,.28),transparent 65%)}
.install-copy{left:622px;top:1285px;width:470px}
.install-copy h2{font-size:27px;line-height:46px}
.install-copy h4{font-size:17px;margin-top:10px}
.install-copy p{font-size:14px;line-height:34px;color:var(--muted);margin-top:16px}

.feature-card{top:1834px;height:203px;background:var(--card);border-radius:8px;padding:30px 30px}
.feature-card h3{font-size:17px;margin-top:6px}
.feature-card p{font-size:14px;line-height:34px;color:var(--muted);margin-top:10px}
.feature-card .card-go{position:absolute;right:20px;bottom:20px;background:linear-gradient(135deg,var(--btn-a),var(--btn-b))}

.promise-card{top:2577px;width:441px;height:233px;background:var(--card);border-radius:8px;padding:38px 44px}
.promise-card h3{font-size:17px}
.promise-card p{font-size:13px;color:var(--muted);margin-top:16px}
.rating-glow{left:150px;top:2850px;width:900px;height:260px;background:radial-gradient(ellipse at center,rgba(90,50,200,.22),transparent 70%)}
.stars{top:2903px;font-size:22px;color:var(--star);letter-spacing:3px}
.rating-text{top:2957px;font-size:19px;line-height:43px}

.faq{left:287px;width:626px}
.faq-item{position:absolute;left:0;width:626px;height:40px;border-bottom:1px solid var(--line);display:flex;justify-content:space-between;font-size:13px;letter-spacing:.6px;color:#bdbac3;text-transform:uppercase}
.faq-item.open{color:var(--purple)}
.faq-answer{position:absolute;left:0;font-size:13px;color:var(--muted)}

.footer{position:absolute;left:0;top:3882px;width:1200px;height:349px;background:var(--bg-footer);text-align:center;font-size:13px;color:var(--muted)}
.footer p{position:absolute;left:0;width:1200px;line-height:34px}
.footer .legal-links{color:#fff;font-weight:500}
</style>
</head>
<body>

<header class="hero">
  <div class="abs brand"><span class="brand-dot"></span>VOXWELL</div>
  <h1 class="abs hero-title"><span class="hl-purple">AI Voice Agents</span> that answer calls, book appts, send emails, text messages, follow up reminders, transfer calls &amp; more for you <span class="hl-blue">24 hours 7 days a week!</span></h1>
  <p class="abs hero-copy">We Will Create An Ai Agent Customized For Your Business At No Cost. Simply Click The Button Above And Your Very Own Ai Agent Will Be Calling You In Just A Couple Minutes. Experience The Magic And Get Ready To Be Very Impressed!</p>
  <a class="abs btn" style="left:112px;top:446px;width:262px" href="#">Get an instant free demo</a>
  <div class="abs hero-art" role="img" aria-label="Futuristic humanoid AI robot head in blue and purple light"></div>
</header>

<section class="workforce">
  <h2 class="abs center section-title" style="top:62px">Meet your new <span class="hl-purple">AI-powered</span> workforce</h2>
  <p class="abs lede" style="left:164px;top:121px;width:872px;text-align:center">We Will Create An Ai Agent Customized For Your Business At No Cost. Simply Click The Button Above And Your Very Own Ai Agent Will Be Calling You In Just A Couple Minutes. Experience The Magic And Get Ready To Be Very Impressed!</p>
  <a class="abs btn btn-center" style="top:223px" href="#">Get an instant free demo</a>
</section>

<span class="abs nav-arrow" style="left:40px">&#8592;</span>
<span class="abs nav-arrow" style="left:1130px">&#8594;</span>

<article class="abs agent-card" style="left:112px">
  <div class="icon-dot"><svg width="24" height="24" viewBox="0 0 24 24" fill="none" stroke="#fff" stroke-width="1.6"><circle cx="12" cy="8" r="4"/><path d="M4 21c1-4 4-6 8-6s7 2 8 6"/></svg></div>
  <h3>AI Receptionist</h3>
  <p>Takes Overflow and After Hours Calls or Can Take Calls 24/7 &amp; Transfer</p>
</article>
<article class="abs agent-card" style="left:448px">
  <div class="icon-dot"><svg width="24" height="24" viewBox="0 0 24 24" fill="none" stroke="#fff" stroke-width="1.6"><circle cx="10" cy="8" r="4"/><path d="M3 21c1-4 3-6 7-6s6 2 7 6"/><circle cx="18" cy="7" r="3"/></svg></div>
  <h3>AI Sales Agent</h3>
  <p>Brian will take your inbound sales calls. Will give all detailed information</p>
  <div class="abs card-go" style="right:0;bottom:0;width:40px;height:40px;border-radius:20px 0 8px 0"><svg width="12" height="12" viewBox="0 0 12 12" fill="none" stroke="#fff" stroke-width="1.6"><path d="M4 2l4 4-4 4"/></svg></div>
</article>
<article class="abs agent-card" style="left:783px">
  <div class="icon-dot"><svg width="24" height="24" viewBox="0 0 24 24" fill="none" stroke="#fff" stroke-width="1.6"><rect x="4" y="5" width="16" height="15" rx="2"/><path d="M4 10h16M8 3v4M16 3v4"/></svg></div>
  <h3>AI Appointment Setter</h3>
  <p>Bobby offers business advice, helps brainstorm ideas, and provides insights</p>
</article>

<div class="abs install-glow"></div>
<div class="abs install-art" role="img" aria-label="Friendly white astronaut-style robot on a purple background"></div>
<div class="abs install-copy">
  <h2>Install the <span class="hl-purple">power of AI</span> for your business</h2>
  <h4>Your wish is their command</h4>
  <p>Your New Ai Agents Will Never Call In Sick And Will Never Complain!</p>
  <p>With your new team of AI Agents, handling inbound calls, sending emails and sms messages, booking appointments and handling customer service inquiries is going to save you a ton of time and money.</p>
</div>

<h2 class="abs center section-title" style="top:1745px">An employee that <span class="hl-blue">never gets</span> sick!</h2>
<article class="abs feature-card" style="left:112px;width:262px">
  <h3>Trained in seconds</h3><p>Learns Your Entire Website In Seconds</p>
  <div class="card-go"><svg width="14" height="14" viewBox="0 0 14 14" fill="none" stroke="#fff" stroke-width="1.6"><path d="M3 11L11 3M5 3h6v6"/></svg></div>
</article>
<article class="abs feature-card" style="left:394px;width:410px">
  <h3>User-friendly</h3><p>Your Ai Agents Sound As If They're Real Humans</p>
  <div class="card-go"><svg width="14" height="14" viewBox="0 0 14 14" fill="none" stroke="#fff" stroke-width="1.6"><path d="M3 11L11 3M5 3h6v6"/></svg></div>
</article>
<article class="abs feature-card" style="left:826px;width:262px">
  <h3>Worldwide</h3><p>Works Anywhere In The Globe</p>
  <div class="card-go"><svg width="14" height="14" viewBox="0 0 14 14" fill="none" stroke="#fff" stroke-width="1.6"><path d="M3 11L11 3M5 3h6v6"/></svg></div>
</article>

<h2 class="abs center section-title" style="top:2116px">Our AI agents <span class="hl-blue">our ready</span> to be hired</h2>
<p class="abs lede" style="left:164px;top:2174px;width:872px;text-align:center">We Will Create An Ai Agent Customized For Your Business At No Cost. Simply Click The Button Above And Your Very Own Ai Agent Will Be Calling You In Just A Couple Minutes. Experience The Magic And Get Ready To Be Very Impressed!</p>
<h3 class="abs center" style="top:2265px;font-size:19px">Lightning-fast responses</h3>
<p class="abs center" style="top:2311px;font-size:13px;color:var(--muted)">Instant answers, no coffee, bathroom or lunch breaks needed</p>
<a class="abs btn btn-center" style="top:2374px" href="#">Get an instant free demo</a>

<h2 class="abs center section-title" style="top:2491px">Our <span class="hl-purple">promise</span> to you</h2>
<article class="abs promise-card" style="left:135px">
  <div class="icon-dot" style="width:64px;height:64px;margin-left:2px"><svg width="30" height="30" viewBox="0 0 24 24" fill="none" stroke="#fff" stroke-width="1.5"><circle cx="12" cy="12" r="8"/><path d="M8.5 12l2.5 2.5 4.5-5"/></svg></div>
  <h3 style="margin-top:36px">14-day money-back guarantee*</h3>
</article>
<article class="abs promise-card" style="left:624px;padding-top:24px">
  <div class="icon-dot" style="width:64px;height:64px"><svg width="30" height="30" viewBox="0 0 24 24" fill="none" stroke="#fff" stroke-width="1.5"><path d="M5 13v-2a7 7 0 0114 0v2"/><rect x="3" y="12" width="4" height="6" rx="1"/><rect x="17" y="12" width="4" height="6" rx="1"/></svg></div>
  <h3 style="margin-top:26px">24/7 customer support</h3>
  <p>Often praised for our friendly &amp; helpful support team</p>
</article>

<div class="abs rating-glow"></div>
<div class="abs center stars">&#9733;&#9733;&#9733;&#9733;&#9733;</div>
<h3 class="abs center rating-text">After our customers have a conversation with their new<br><span class="hl-blue">AI voice agent</span> they give us 5 stars!</h3>

<h2 class="abs center section-title" style="top:3154px">Do you have <span class="hl-purple">questions?</span></h2>
<div class="abs faq" style="top:3233px">
  <div class="faq-item" style="top:0"><span>What exactly are the AI voice agents?</span><span>+</span></div>
  <div class="faq-item" style="top:79px"><span>How will these AI voice agents benefit?</span><span>+</span></div>
  <div class="faq-item open" style="top:156px"><span>Are they easy to use?</span><span>&minus;</span></div>
  <p class="faq-answer" style="top:222px">We provide a done for you service. We create your AI Voice Agent and launch it within days!</p>
</div>

<h2 class="abs center section-title" style="top:3543px;line-height:46px">These AI agents can help your <span class="hl-purple">business tremendously.</span><br>Imagine the possibilities</h2>
<p class="abs lede" style="left:164px;top:3652px;width:872px;text-align:center">We Will Create An Ai Agent Customized For Your Business At No Cost. Simply Click The Button Above And Your Very Own Ai Agent Will Be Calling You In Just A Couple Minutes. Experience The Magic And Get Ready To Be Very Impressed!</p>
<a class="abs btn btn-center" style="top:3756px" href="#">Get an instant free demo</a>

<footer class="footer">
  <p style="top:36px;left:200px;width:800px">*14-Day Money Back Guarantee Terms: If you use the ai agents and you're not happy. Then you can contact us in the first 14 days for a full refund.</p>
  <p style="top:141px">Do you have questions about ( ) Please email ( )</p>
  <p style="top:158px;left:200px;width:800px;padding-top:8px">&nbsp;</p>
  <p style="top:166px;left:200px;width:800px">IMPORTANT: This site is not a part of the Friendgrid website or Friendgrid Inc. Additionally, this site is NOT endorsed by Friendgrid in any way. FRIENDGRID is a trademark of FRIENDGRID, Inc.</p>
  <p style="top:239px;color:#fff">&copy; 2025 VOXWELL AI</p>
  <p class="legal-links" style="top:280px">PRIVACY | TERMS &amp; CONDITIONS | EARNINGS &amp; PRODUCTS DISCLAIMER</p>
</footer>

</body>
</html>
```